Business card design for my company.
I would like the card's background colour to be black. You can also see our web site to get an idea of our brand. https://www.tmwhomecrafting.com.au/
- Name
- Email

```html
<!DOCTYPE html>
<html lang="en">
<head>
<meta charset="utf-8">
<title>TMW Home Crafting – Business Card</title>
<link rel="stylesheet" href="https://fonts.googleapis.com/css2?family=Roboto:wght@400;500;700&display=swap">
<style>
  :root {
    --stage: #2b2b2b;
    --card-dark: #1f1f20;
    --card-light: #f7f7f5;
    --brand-green: #119a45;
    --ink: #1b1b1b;
    --muted-light: #d9d9d9;
    --logo-dark: #3a3a3b;
  }
  * { box-sizing: border-box; margin: 0; padding: 0; }
  html, body { width: 1200px; height: 852px; overflow: hidden; }
  body {
    background: var(--stage);
    font-family: "Roboto", Arial, sans-serif;
    display: flex;
    align-items: center;
    justify-content: center;
    gap: 60px;
  }
  .card {
    width: 504px;
    height: 288px;
    border-radius: 18px;
    position: relative;
    overflow: hidden;
    border-bottom: 7px solid var(--brand-green);
  }
  .card--back { background: var(--card-dark); }
  .card--front { background: var(--card-light); }

  .wordmark {
    display: flex;
    align-items: center;
    gap: 10px;
    font-weight: 700;
    letter-spacing: 1px;
    text-transform: uppercase;
    white-space: nowrap;
  }
  .wordmark__square { width: 16px; height: 16px; flex: none; }

  .card--back .wordmark {
    position: absolute;
    top: 104px;
    left: 0; right: 0;
    justify-content: center;
    font-size: 30px;
    color: var(--logo-dark);
  }
  .card--back .wordmark__square { background: var(--logo-dark); }
  .card--back .website {
    position: absolute;
    bottom: 22px;
    left: 0; right: 0;
    text-align: center;
    font-size: 13px;
    color: var(--muted-light);
  }

  .card--front .wordmark {
    position: absolute;
    left: 28px;
    top: 176px;
    width: 236px;
    font-size: 16px;
    gap: 8px;
    color: var(--ink);
  }
  .card--front .wordmark__square { width: 14px; height: 14px; background: var(--brand-green); }

  .contact {
    position: absolute;
    left: 284px;
    top: 52px;
    right: 16px;
    color: var(--ink);
  }
  .contact__name {
    font-size: 22px;
    font-weight: 500;
    color: var(--brand-green);
  }
  .contact__role { font-size: 13px; margin-top: 2px; }
  .contact__list { list-style: none; margin-top: 18px; }
  .contact__list li {
    display: flex;
    align-items: center;
    gap: 10px;
    font-size: 12.5px;
    line-height: 20px;
    white-space: nowrap;
  }
  .contact__list svg { width: 12px; height: 12px; fill: var(--brand-green); flex: none; }
</style>
</head>
<body>
  <section class="card card--back">
    <div class="wordmark"><span class="wordmark__square"></span>TMW Home Crafting</div>
    <p class="website">www.tmwhomecrafting.com.au</p>
  </section>

  <section class="card card--front">
    <div class="wordmark"><span class="wordmark__square"></span>TMW Home Crafting</div>
    <div class="contact">
      <h1 class="contact__name">Liam Hartley</h1>
      <p class="contact__role">General Manager</p>
      <ul class="contact__list">
        <li><svg viewBox="0 0 24 24"><path d="M6.6 10.8a15.1 15.1 0 0 0 6.6 6.6l2.2-2.2a1 1 0 0 1 1-.25 11.4 11.4 0 0 0 3.6.57 1 1 0 0 1 1 1V20a1 1 0 0 1-1 1A17 17 0 0 1 3 4a1 1 0 0 1 1-1h3.5a1 1 0 0 1 1 1c0 1.25.2 2.45.57 3.57a1 1 0 0 1-.25 1z"/></svg>0400 123 456</li>
        <li><svg viewBox="0 0 24 24"><path d="M2 5h20v14H2zm2 2v.5l8 5 8-5V7l-8 5z"/></svg>info@tmwhomecrafting.com.au</li>
        <li><svg viewBox="0 0 24 24"><path d="M12 2a10 10 0 1 0 0 20 10 10 0 0 0 0-20zm0 2c.9 1.2 1.6 2.6 2 4h-4c.4-1.4 1.1-2.8 2-4zM4.3 14a8 8 0 0 1 0-4h3.3a16 16 0 0 0 0 4zm.8 2h3a13 13 0 0 0 1.3 3.3A8 8 0 0 1 5.1 16zm3-8h-3a8 8 0 0 1 4.3-3.3A13 13 0 0 0 8.1 8zM12 20c-.9-1.2-1.6-2.6-2-4h4c-.4 1.4-1.1 2.8-2 4zm2.3-6H9.7a14 14 0 0 1 0-4h4.6a14 14 0 0 1 0 4zm.3 5.3A13 13 0 0 0 15.9 16h3a8 8 0 0 1-4.3 3.3zm1.8-5.3a16 16 0 0 0 0-4h3.3a8 8 0 0 1 0 4z"/></svg>www.tmwhomecrafting.com.au</li>
        <li><svg viewBox="0 0 24 24"><path d="M12 2a7 7 0 0 0-7 7c0 5.2 7 13 7 13s7-7.8 7-13a7 7 0 0 0-7-7zm0 9.5A2.5 2.5 0 1 1 12 6.5a2.5 2.5 0 0 1 0 5z"/></svg>Riverton, Tasmania, Australia</li>
      </ul>
    </div>
  </section>
</body>
</html>
```